Coastline Premier Retreats Business Card Design

Design a business card for Coastline Premier Retreats. Look at the website for colors and reference. Card should have logo, name, title, office number, mobile number, email, URL and a tagline like, "Luxury Hotel & Resort Email Marketing" (This might change).

https://www.coastlinepremierretreats.example

The rest I will leave up to your imagination.

Contact Information for Business Card

Logo, name, title, office number, mobile number, email, URL and a tagline like, "Luxury Hotel & Resort Email Marketing" (This might change).

```html
<!DOCTYPE html>
<html lang="en">
<head>
<meta charset="utf-8">
<title>Coastline Premier Retreats – Business Card</title>
<link rel="stylesheet" href="https://fonts.googleapis.com/css2?family=Montserrat:wght@400;600;700;800&display=swap">
<style>
  :root {
    --bg: #2a2b2f;
    --ink: #111111;
    --black: #050505;
    --white: #ffffff;
    --orange: #f07423;
    --graphite: #3b3c3f;
  }
  * { margin: 0; padding: 0; box-sizing: border-box; }
  html, body { width: 1200px; height: 900px; overflow: hidden; }
  body {
    background: var(--bg);
    font-family: "Montserrat", sans-serif;
    position: relative;
  }
  .card {
    position: absolute;
    left: 300px;
    width: 600px;
    height: 343px;
    border-radius: 18px;
    overflow: hidden;
    box-shadow: 0 18px 40px rgba(0,0,0,.45);
  }
  .card-front { top: 60px; background: var(--black); color: var(--white); }
  .card-back { top: 470px; background: var(--white); color: var(--ink); }
  .card-shapes { position: absolute; inset: 0; width: 100%; height: 100%; }

  .brand {
    position: absolute;
    display: flex;
    align-items: center;
    gap: 12px;
    font-weight: 800;
    text-transform: uppercase;
    letter-spacing: .5px;
    line-height: 1.05;
    white-space: nowrap;
  }
  .brand-mark { width: 16px; height: 16px; flex: none; }
  .card-front .brand { left: 150px; top: 100px; font-size: 30px; color: var(--white); }
  .card-front .brand-mark { background: var(--white); }
  .card-back .brand { left: 60px; top: 70px; font-size: 28px; color: var(--ink); }
  .card-back .brand-mark { background: var(--orange); }

  .tagline {
    position: absolute;
    left: 40px;
    top: 289px;
    font-size: 13px;
    font-weight: 700;
    color: var(--white);
    white-space: nowrap;
  }

  .person { position: absolute; left: 60px; top: 250px; }
  .person-name { font-size: 24px; font-weight: 800; color: var(--orange); line-height: 1; white-space: nowrap; }
  .person-title { font-size: 13px; font-weight: 400; color: var(--ink); margin-top: 4px; padding-left: 120px; }

  .contacts {
    position: absolute;
    left: 318px;
    top: 196px;
    list-style: none;
    font-size: 11px;
    font-weight: 400;
    white-space: nowrap;
  }
  .contacts li { display: flex; align-items: center; gap: 7px; margin-bottom: 8px; }
  .contact-icon { width: 18px; height: 18px; flex: none; }
</style>
</head>
<body>

  <section class="card card-front" aria-label="Card front">
    <svg class="card-shapes" viewBox="0 0 600 343" aria-hidden="true">
      <polygon points="0,280 340,280 318,312 0,312" fill="var(--orange)"/>
      <polygon points="360,240 600,240 600,272 338,272" fill="var(--graphite)"/>
      <line x1="0" y1="322" x2="600" y2="322" stroke="var(--orange)" stroke-width=".8" opacity=".5"/>
    </svg>
    <div class="brand"><span class="brand-mark"></span><span>Coastline Premier<br>Retreats</span></div>
    <p class="tagline">Luxury Hotel &amp; Resort Email Marketing</p>
  </section>

  <section class="card card-back" aria-label="Card back">
    <svg class="card-shapes" viewBox="0 0 600 343" aria-hidden="true">
      <polygon points="0,170 330,170 308,205 0,205" fill="var(--orange)"/>
      <polygon points="350,140 600,140 600,170 330,170" fill="var(--graphite)"/>
    </svg>
    <div class="brand"><span class="brand-mark"></span><span>Coastline Premier<br>Retreats</span></div>

    <div class="person">
      <p class="person-name">Jonah Mercer</p>
      <p class="person-title">Owner</p>
    </div>

    <ul class="contacts">
      <li>
        <svg class="contact-icon" viewBox="0 0 20 20" aria-hidden="true"><circle cx="10" cy="10" r="10" fill="var(--orange)"/><path d="M6 8c0-1 1-2 2-2h4c1 0 2 1 2 2l-1.5 1H7.5z M6.5 10h7v3.5h-7z" fill="var(--white)"/></svg>
        <span>555.014.2290 x 204</span>
      </li>
      <li>
        <svg class="contact-icon" viewBox="0 0 20 20" aria-hidden="true"><circle cx="10" cy="10" r="10" fill="var(--orange)"/><rect x="7" y="4.5" width="6" height="11" rx="1.2" fill="none" stroke="var(--white)" stroke-width="1.4"/></svg>
        <span>555.019.4417</span>
      </li>
      <li>
        <svg class="contact-icon" viewBox="0 0 20 20" aria-hidden="true"><circle cx="10" cy="10" r="10" fill="var(--orange)"/><rect x="5" y="6.5" width="10" height="7" fill="var(--white)"/><path d="M5 6.5l5 4 5-4" fill="none" stroke="var(--orange)" stroke-width="1"/></svg>
        <span>info@coastlinepremierretreats.example</span>
      </li>
      <li>
        <svg class="contact-icon" viewBox="0 0 20 20" aria-hidden="true"><circle cx="10" cy="10" r="10" fill="var(--orange)"/><circle cx="10" cy="10" r="5" fill="none" stroke="var(--white)" stroke-width="1.3"/><path d="M5 10h10M10 5c-2 3-2 7 0 10M10 5c2 3 2 7 0 10" fill="none" stroke="var(--white)" stroke-width="1"/></svg>
        <span>www.coastlinepremierretreats.example</span>
      </li>
    </ul>
  </section>

</body>
</html>
```